Business Card Design

New business card design

Target Market(s)

Residential & Commercial Property Managers

Industry/Entity Type

Plumbing Services

Contact Information for Business Card

Name - Rowan Keddle, title - Director, Phone Number - 0431 286 517, email - rowan@tbk-plumbing.com.au, Company ABN - 73 215 904 386,

Font styles to use
Sans Serif

Colors
0054AA
0677BA
7BADD7
CADEEF
E8F1F8

```html
<!DOCTYPE html>
<html lang="en">
<head>
<meta charset="utf-8">
<title>TBK Plumbing Services – Business Card</title>
<link rel="stylesheet" href="https://fonts.googleapis.com/css2?family=Poppins:wght@300;400;500;600&display=swap">
<style>
  :root {
    --page-bg: #d9cfc2;
    --card-bg: #e7e1d8;
    --card-edge: #f3efe9;
    --ink-dark: #1c2326;
    --ink-soft: #4a4540;
    --teal: #1a8ea9;
    --band-dark-a: #262a2c;
    --band-dark-b: #383d40;
    --band-brown: #5c4d3f;
    --band-text: #e6ddd2;
    --drop-rim: #c9b9a6;
  }
  * { box-sizing: border-box; margin: 0; padding: 0; }
  html, body {
    width: 1200px; height: 1046px; overflow: hidden;
    background: var(--page-bg);
    font-family: "Poppins", sans-serif;
  }
  .business-card {
    position: absolute; left: 100px; top: 250px;
    width: 1000px; height: 545px;
    background: var(--card-bg);
    border: 1px solid var(--card-edge);
    border-radius: 34px;
    overflow: hidden;
    box-shadow: 0 10px 30px rgba(60, 45, 30, 0.18);
  }
  .brand {
    position: absolute; left: 0; right: 0; top: 20px;
    text-align: center;
  }
  .brand-name {
    display: block;
    font-size: 96px; font-weight: 400; line-height: 1;
    color: var(--ink-dark);
    letter-spacing: 6px;
  }
  .brand-tagline {
    display: block; margin-top: 36px;
    font-size: 16px; font-weight: 400;
    color: var(--ink-soft);
    letter-spacing: 15px;
  }
  .info-band {
    position: absolute; left: 0; right: 0; top: 327px; height: 128px;
    background: var(--band-brown);
  }
  .info-band .band-dark {
    position: absolute; left: 0; top: 0; bottom: 0; width: 496px;
    background: linear-gradient(90deg, var(--band-dark-a), var(--band-dark-b) 55%, var(--band-dark-a));
  }
  .band-mark {
    position: absolute; left: 447px; top: 10px;
    width: 108px; height: 108px;
    border-radius: 50%;
    background: var(--teal);
    border: 5px solid var(--drop-rim);
  }
  .person {
    position: absolute; right: 572px; top: 22px;
    text-align: right;
  }
  .person-name {
    font-size: 43px; font-weight: 400; line-height: 1.1;
    color: var(--teal);
  }
  .person-name .first { font-weight: 600; }
  .person-title {
    font-size: 21px; font-weight: 500;
    color: var(--band-text);
    margin-top: 2px;
  }
  .contacts {
    position: absolute; left: 587px; top: 18px;
    list-style: none;
  }
  .contacts li {
    display: flex; align-items: center;
    height: 31px;
    font-size: 21px; font-weight: 300;
    color: var(--band-text);
  }
  .contacts svg { width: 19px; height: 19px; margin-right: 14px; flex: none; }
  .abn {
    position: absolute; left: 0; right: 0; top: 476px;
    text-align: center;
    font-size: 21px; font-weight: 400;
    color: var(--teal);
  }
</style>
</head>
<body>
  <section class="business-card">
    <header class="brand">
      <span class="brand-name">tbk</span>
      <span class="brand-tagline">plumbing services</span>
    </header>

    <div class="info-band">
      <div class="band-dark"></div>
      <div class="person">
        <p class="person-name"><span class="first">Rowan</span> Keddle</p>
        <p class="person-title">Director</p>
      </div>
      <div class="band-mark"></div>
      <ul class="contacts">
        <li>
          <svg viewBox="0 0 24 24" fill="#1a8ea9" aria-hidden="true"><path d="M6.6 10.8a15 15 0 0 0 6.6 6.6l2.2-2.2c.3-.3.7-.4 1-.2 1.1.4 2.3.6 3.6.6.6 0 1 .4 1 1V20c0 .6-.4 1-1 1A17 17 0 0 1 3 4c0-.6.4-1 1-1h3.5c.6 0 1 .4 1 1 0 1.3.2 2.5.6 3.6.1.3 0 .7-.2 1z"/></svg>
          0431 286 517
        </li>
        <li>
          <svg viewBox="0 0 24 24" fill="#1a8ea9" aria-hidden="true"><path d="M2 6h20v13H2z" opacity=".9"/><path d="M2 6l10 7 10-7" fill="none" stroke="#5c4d3f" stroke-width="1.6"/></svg>
          www.tbk-plumbing.com.au
        </li>
        <li>
          <svg viewBox="0 0 24 24" aria-hidden="true"><circle cx="12" cy="12" r="10" fill="#1a8ea9"/><path d="M2 12h20M12 2c3 3 3 17 0 20M12 2c-3 3-3 17 0 20" fill="none" stroke="#5c4d3f" stroke-width="1.3"/></svg>
          rowan@tbk-plumbing.com.au
        </li>
      </ul>
    </div>

    <p class="abn">ABN - 73 215 904 386</p>
  </section>
</body>
</html>
```